Energy Company needs a Business Card Design

We need a business card design for a new company based in Singapore called Tavren Energy. Tavren Energy is a producer of renewable energies largely for the biofuels market. Sourced entirely from sustainable resources, Tavren Energy aims to be a fully integrated oil company operating in 100% sustainable way. We would like to see designs that use the same colours as the attached file.

Industry/Entity Type

Business

```html
<!DOCTYPE html>
<html lang="en">
<head>
<meta charset="utf-8">
<title>Tavren Energy – Business Card</title>
<link href="https://fonts.googleapis.com/css2?family=Montserrat:wght@400;500;700&display=swap" rel="stylesheet">
<style>
  :root {
    --bg: #d9d8d4;
    --card-white: #ffffff;
    --card-black: #0d0d0d;
    --card-black-soft: #262626;
    --leaf-green: #8cc63f;
    --silver-light: #f2f2f2;
    --silver-mid: #c9c9c9;
    --logo-grey: #8a8a8a;
    --ink-dark: #222222;
    --text-light: #ffffff;
  }
  * { box-sizing: border-box; margin: 0; padding: 0; }
  html, body { width: 1200px; height: 900px; overflow: hidden; }
  body {
    background: var(--bg);
    font-family: "Montserrat", Arial, sans-serif;
    position: relative;
  }
  .card {
    position: absolute;
    left: 250px;
    width: 700px;
    height: 400px;
    border-radius: 26px;
    overflow: hidden;
    box-shadow: 0 8px 22px rgba(0,0,0,0.25);
  }
  /* Back side */
  .card-back {
    top: 30px;
    background: radial-gradient(ellipse at 50% 40%, var(--card-black-soft), var(--card-black) 75%);
    display: flex;
    align-items: center;
    justify-content: center;
  }
  .brand-mark {
    display: flex;
    align-items: center;
    gap: 14px;
    font-weight: 500;
    letter-spacing: 3px;
    text-transform: uppercase;
    color: var(--logo-grey);
    white-space: nowrap;
  }
  .brand-mark .dot {
    width: 20px; height: 20px; border-radius: 50%;
    background: var(--leaf-green);
  }
  .card-back .brand-mark { font-size: 40px; letter-spacing: 4px; color: #b5b5b5; }

  /* Front side */
  .card-front {
    top: 470px;
    background: var(--card-white);
  }
  .card-front svg.panel { position: absolute; inset: 0; }
  .card-front .brand-mark {
    position: absolute;
    left: 50px;
    top: 176px;
    font-size: 27px;
  }
  .name-band {
    position: absolute;
    left: 448px;
    top: 42px;
    width: 252px;
    height: 66px;
    background: linear-gradient(180deg, var(--silver-light), var(--silver-mid));
    padding: 11px 0 0 30px;
  }
  .name-band .name {
    font-weight: 700;
    font-size: 21px;
    color: var(--leaf-green);
    letter-spacing: 1px;
  }
  .name-band .title {
    font-size: 13px;
    color: var(--ink-dark);
    letter-spacing: 1.5px;
  }
  .contact {
    position: absolute;
    left: 474px;
    top: 148px;
    color: var(--text-light);
    font-size: 13px;
    letter-spacing: 0.6px;
    line-height: 1.55;
    white-space: nowrap;
  }
  .contact .address { margin-bottom: 10px; }
  .contact ul { list-style: none; }
  .contact li { display: flex; align-items: center; gap: 10px; }
  .contact svg { width: 12px; height: 12px; flex: none; }
</style>
</head>
<body>

  <section class="card card-back" aria-label="Card back">
    <div class="brand-mark"><span class="dot"></span>Tavren Energy</div>
  </section>

  <section class="card card-front" aria-label="Card front">
    <svg class="panel" viewBox="0 0 700 400" width="700" height="400">
      <defs>
        <linearGradient id="blackPanel" x1="0" y1="0" x2="1" y2="1">
          <stop offset="0" stop-color="#050505"/>
          <stop offset="0.6" stop-color="#1a1a1a"/>
          <stop offset="1" stop-color="#3a3a3a"/>
        </linearGradient>
      </defs>
      <path d="M470 0 Q360 190 500 400 L700 400 L700 0 Z" fill="url(#blackPanel)"/>
      <path d="M470 0 Q360 190 500 400" fill="none" stroke="var(--leaf-green)" stroke-width="6"/>
    </svg>

    <div class="brand-mark"><span class="dot"></span>Tavren Energy</div>

    <div class="name-band">
      <div class="name">Marcus Hale</div>
      <div class="title">President</div>
    </div>

    <div class="contact">
      <div class="address">48 Harbour Lane<br>Riverside, AB 20417</div>
      <ul>
        <li>
          <svg viewBox="0 0 12 12"><rect x="3" y="0.5" width="6" height="11" rx="1.2" fill="none" stroke="#8cc63f" stroke-width="1.3"/><rect x="4.5" y="2" width="3" height="5" fill="#8cc63f"/></svg>
          +2222. 345. 678
        </li>
        <li>
          <svg viewBox="0 0 12 12"><path d="M2.5 1 L5 3.5 L3.8 5 Q5 7.5 7 8.2 L8.5 7 L11 9.5 L9.5 11 Q4 10.5 1 2.5 Z" fill="#8cc63f"/></svg>
          +2222. 345. 679
        </li>
        <li>
          <svg viewBox="0 0 12 12"><rect x="0.7" y="2.2" width="10.6" height="7.6" fill="none" stroke="#8cc63f" stroke-width="1.2"/><path d="M0.7 2.2 L6 6.5 L11.3 2.2" fill="none" stroke="#8cc63f" stroke-width="1.2"/></svg>
          info@tavrenenergy.com
        </li>
        <li>
          <svg viewBox="0 0 12 12"><circle cx="6" cy="6" r="5.2" fill="none" stroke="#8cc63f" stroke-width="1.2"/><ellipse cx="6" cy="6" rx="2.2" ry="5.2" fill="none" stroke="#8cc63f" stroke-width="1"/><line x1="0.8" y1="6" x2="11.2" y2="6" stroke="#8cc63f" stroke-width="1"/></svg>
          www.tavrenenergy.com
        </li>
      </ul>
    </div>
  </section>

</body>
</html>
```